IT Company requires new Business Card design.

Over the years we have had a few different business card designs. We are now due for new cards across the board for all staff. We felt this would be a good time to start fresh with a new design. Our traditional card simply had our details on the front, and a list of services on the back. We don't particularly need the list of services, we have had cards where the only thing on the rear of the card was our logo.
Feel free to be creative, we would like our tag line "Complete IT Management" to appear at some point, doesn't necessarily have to be with the logo.
I have attached samples and drafts of various previous cards we have used over the years.

```html
<!DOCTYPE html>
<html lang="en">
<head>
<meta charset="utf-8">
<title>Ridgeway Networking – Business Card</title>
<link href="https://fonts.googleapis.com/css2?family=Source+Sans+3:wght@400;600;700&display=swap" rel="stylesheet">
<style>
  :root {
    --backdrop: #e6e4e1;
    --card-dark: #2b2b2b;
    --card-mid: #3c3c3c;
    --card-light: #4a4a4a;
    --white: #ffffff;
    --text-soft: #e4e4e4;
    --silver: #b9b9b9;
    --silver-dark: #8f8f8f;
    --divider: #9a9a9a;
  }
  * { margin: 0; padding: 0; box-sizing: border-box; }
  html, body {
    width: 1200px; height: 720px; overflow: hidden;
    background: var(--backdrop);
    font-family: "Source Sans 3", "Helvetica Neue", Arial, sans-serif;
  }
  .canvas { position: relative; width: 1200px; height: 720px; }

  .card {
    position: absolute; top: 205px; width: 540px; height: 310px;
    border-radius: 3px; overflow: hidden; color: var(--white);
    background:
      repeating-linear-gradient(0deg, rgba(255,255,255,0.018) 0 1px, rgba(0,0,0,0.03) 1px 2px, transparent 2px 3px),
      radial-gradient(ellipse at 45% 40%, var(--card-light) 0%, var(--card-mid) 45%, var(--card-dark) 100%);
    box-shadow: 0 6px 18px rgba(0,0,0,0.22);
  }
  .card--front { left: 40px; }
  .card--back { left: 620px; }

  /* Front */
  .brand { position: absolute; left: 30px; top: 30px; display: flex; align-items: flex-start; gap: 14px; }
  .brand__square { width: 58px; height: 58px; background: var(--silver); margin-top: 4px; }
  .brand__name {
    font-weight: 700; font-size: 30px; line-height: 0.95; letter-spacing: 0.5px;
    text-transform: uppercase; color: var(--white);
  }
  .brand__tagline {
    margin-top: 6px; font-size: 9.5px; font-weight: 600; letter-spacing: 3.2px;
    text-transform: uppercase; color: var(--text-soft);
  }

  .person { position: absolute; left: 30px; top: 192px; }
  .person__name { font-size: 17px; font-weight: 700; }
  .person__role { font-size: 14px; color: var(--text-soft); margin-top: 1px; }

  .web { font-size: 15px; color: var(--text-soft); letter-spacing: 0.2px; }
  .card--front .web { position: absolute; left: 30px; bottom: 26px; }

  .contact {
    position: absolute; left: 300px; top: 132px; padding-left: 12px;
    border-left: 1px solid var(--divider); font-size: 13px; line-height: 1.5; color: var(--text-soft);
  }
  .contact__row { display: flex; align-items: center; gap: 6px; }
  .contact__row svg { width: 11px; height: 11px; fill: var(--text-soft); flex: none; }
  .contact__address { margin-top: 12px; line-height: 1.3; }

  /* Back */
  .back-name {
    position: absolute; left: 0; right: 0; top: 78px; text-align: center;
    font-weight: 700; font-size: 52px; line-height: 0.95; letter-spacing: 1px;
    text-transform: uppercase; color: var(--silver);
  }
  .card--back .web { position: absolute; left: 0; right: 0; bottom: 30px; text-align: center; }
</style>
</head>
<body>
<main class="canvas">

  <section class="card card--front" aria-label="Business card front">
    <div class="brand">
      <div class="brand__square"></div>
      <div>
        <div class="brand__name">Ridgeway<br>Networking</div>
        <div class="brand__tagline">Complete IT Management</div>
      </div>
    </div>

    <div class="person">
      <div class="person__name">Daniel Marsh</div>
      <div class="person__role">Operation Manager</div>
    </div>

    <div class="contact">
      <div class="contact__row">
        <svg viewBox="0 0 24 24" aria-hidden="true"><path d="M6.6 10.8a15 15 0 0 0 6.6 6.6l2.2-2.2a1 1 0 0 1 1-.25 11.4 11.4 0 0 0 3.6.57 1 1 0 0 1 1 1V20a1 1 0 0 1-1 1A17 17 0 0 1 3 4a1 1 0 0 1 1-1h3.5a1 1 0 0 1 1 1c0 1.25.2 2.45.57 3.57a1 1 0 0 1-.25 1z"/></svg>
        <span>08 5550 1834</span>
      </div>
      <div class="contact__row">
        <svg viewBox="0 0 24 24" aria-hidden="true"><path d="M7 1h10a2 2 0 0 1 2 2v18a2 2 0 0 1-2 2H7a2 2 0 0 1-2-2V3a2 2 0 0 1 2-2zm0 3v14h10V4zm5 15.5a1.2 1.2 0 1 0 0 2.4 1.2 1.2 0 0 0 0-2.4z"/></svg>
        <span>0400 555 718</span>
      </div>
      <div class="contact__row">
        <svg viewBox="0 0 24 24" aria-hidden="true"><path d="M7 2h10v5H7zM4 8h16a2 2 0 0 1 2 2v7h-4v5H6v-5H2v-7a2 2 0 0 1 2-2zm4 8v4h8v-4z"/></svg>
        <span>08 5550 1834</span>
      </div>
      <div class="contact__row">
        <svg viewBox="0 0 24 24" aria-hidden="true"><path d="M2 5h20v14H2zm2 2v.5l8 5 8-5V7zm0 2.8V17h16V9.8l-8 5z"/></svg>
        <span>daniel@ridgewaynetworking.com.au</span>
      </div>
      <div class="contact__address">Unit 4 18 Marlow Street<br>Bayfield WA 6170</div>
    </div>

    <div class="web">www.ridgewaynetworking.com.au</div>
  </section>

  <section class="card card--back" aria-label="Business card back">
    <div class="back-name">Ridgeway<br>Networking</div>
    <div class="web">www.ridgewaynetworking.com.au</div>
  </section>

</main>
</body>
</html>
```